Consultancy Business Card Design

We need a business card design for a new company based in singapore called KestrelOak. KestrelOak a boutique consultancy firm offering broad-based business solutions, from conception to re-invention, for ventures from new start-ups to long-running traditional businesses.
Its 2 main divisions (Food & Beverage Operations and Construction & Project Management) have access to a wide range of networks, knowledge bases, and resources to service its clients across numerous diverse sectors. This includes, and is not limited to, construction, F&B, and retail.
We are a company that combines the ambition, boldness and energy of one in the 20s with the dedication, level-headedness and dependability of one entering its 30s. Bridging the experiences of the old with ideals of the young, we draw on the positives of both to create a unique synergy.
We hope to see designs that fits our company profile.
Industry/Entity Type
Boutique
Contact Information for Business Card
KestrelOak(Company Name)
Marcus Thiel (Name)
Principle Consultant (Title)
F&B and Hospitality (Division)
(+65) 8043 5617 (Contact no.)
marcus@kestreloak.com.sg (Email)
Colors
Designer to choose colors to be used in the design.

```html
<!DOCTYPE html>
<html lang="en">
<head>
<meta charset="utf-8">
<title>KestrelOak Business Card</title>
<link href="https://fonts.googleapis.com/css2?family=Varela+Round&display=swap" rel="stylesheet">
<style>
  :root {
    --page-bg: #e4e4e4;
    --card-white: #f6f6f6;
    --brand-red: #d9232a;
    --brand-black: #1c1c1c;
    --ink-dark: #2b2b2b;
    --ink-light: #ffffff;
  }
  * { box-sizing: border-box; margin: 0; padding: 0; }
  html, body {
    width: 1200px;
    height: 900px;
    overflow: hidden;
    background: var(--page-bg);
    font-family: "Varela Round", "Helvetica Neue", Arial, sans-serif;
  }
  .canvas {
    width: 1200px;
    height: 900px;
    display: flex;
    flex-direction: column;
    align-items: center;
    justify-content: center;
    gap: 30px;
  }
  .card {
    width: 700px;
    height: 400px;
    background: var(--card-white);
    position: relative;
    overflow: hidden;
    display: flex;
    flex-direction: column;
    box-shadow: 0 6px 18px rgba(0,0,0,0.18);
  }
  .wordmark {
    font-size: 46px;
    letter-spacing: 0.5px;
    color: var(--ink-dark);
  }
  /* Front */
  .card-front .logo-area {
    flex: 1;
    display: flex;
    align-items: center;
    justify-content: center;
  }
  .contact-band {
    height: 145px;
    background: var(--brand-red);
    display: grid;
    grid-template-columns: 1fr 1fr 1fr;
    align-items: start;
    padding: 34px 28px 0;
    color: var(--ink-light);
  }
  .contact-item {
    display: flex;
    flex-direction: column;
    align-items: center;
    text-align: center;
    font-size: 13px;
    line-height: 1.45;
  }
  .contact-icon {
    width: 14px;
    height: 14px;
    margin-bottom: 10px;
    fill: var(--ink-light);
  }
  .contact-name { font-size: 14px; }
  .contact-role { opacity: 0.92; }
  /* Back */
  .card-back .top-strip {
    height: 14px;
    background: var(--brand-red);
  }
  .card-back .logo-area {
    flex: 1;
    display: flex;
    align-items: center;
    justify-content: center;
  }
  .card-back .bottom-band {
    height: 150px;
    background: linear-gradient(180deg, #2a2a2a 0%, var(--brand-black) 100%);
  }
</style>
</head>
<body>
<main class="canvas">
  <section class="card card-front" aria-label="Business card front">
    <div class="logo-area">
      <span class="wordmark">KestrelOak</span>
    </div>
    <div class="contact-band">
      <div class="contact-item">
        <svg class="contact-icon" viewBox="0 0 16 16" aria-hidden="true">
          <circle cx="8" cy="4.5" r="3.5"/>
          <path d="M1 16c0-4 3.2-6.5 7-6.5s7 2.5 7 6.5z"/>
        </svg>
        <span class="contact-name">Marcus Thiel</span>
        <span class="contact-role">Principle Consultant -</span>
        <span class="contact-role">F&amp;B and Hospitality</span>
      </div>
      <div class="contact-item">
        <svg class="contact-icon" viewBox="0 0 16 16" aria-hidden="true">
          <path d="M3.6 1.2 6 3.6c.4.4.4 1 0 1.4L4.9 6.1c.8 1.8 3.2 4.2 5 5l1.1-1.1c.4-.4 1-.4 1.4 0l2.4 2.4c.4.4.4 1 0 1.4l-1.2 1.2C11.8 16.8 0 5 1.2 3.2L2.2 1.2c.4-.4 1-.4 1.4 0z"/>
        </svg>
        <span>(+65) 8043 5617</span>
      </div>
      <div class="contact-item">
        <svg class="contact-icon" viewBox="0 0 16 16" aria-hidden="true">
          <path d="M1 3h14v1.2L8 9 1 4.2z"/>
          <path d="M1 5.8 8 10.6l7-4.8V13H1z"/>
        </svg>
        <span>marcus@kestreloak.com.sg</span>
      </div>
    </div>
  </section>

  <section class="card card-back" aria-label="Business card back">
    <div class="top-strip"></div>
    <div class="logo-area">
      <span class="wordmark">KestrelOak</span>
    </div>
    <div class="bottom-band"></div>
  </section>
</main>
</body>
</html>
```